Charity Initiative needs a WebPage design

We need a web design for charity initiative by two young guys riding their bikes around Australia to support HarbourLight which helps people with depression and anxiety. Full brief and requirements are attached in the PDF and word document. We have the logo already done and attached. Website will be done in Wordpress and need to get Donations, display current donations, show live Video feed, GPS tracker, Blogs etc and also ability to sell merchandise later

Target Market(s)

Sponsors, Business, Young People

Number of Pages Required

4 page

Font styles to use
Serif
Sans Serif
Decorative
Script

Requirements
Must have
• As per Brief and also Donation status etc
Nice to have
• Please check my logo and read the Bried

```html
<!DOCTYPE html>
<html lang="en">
<head>
<meta charset="utf-8">
<title>Open Road Ride — supporting HarbourLight</title>
<link rel="stylesheet" href="https://fonts.googleapis.com/css2?family=Raleway:wght@400;500;600&family=Open+Sans:wght@400;600&display=swap">
<style>
:root{
  --pink:#e8175d;
  --pink-dark:#c8104c;
  --orange:#f06a2a;
  --yellow:#f1b20d;
  --teal:#45b3ad;
  --teal-light:#52c2bf;
  --teal-deep:#2e9a9a;
  --ink:#333;
  --muted:#666;
  --line:#ddd;
  --white:#fff;
}
*{box-sizing:border-box;margin:0;padding:0}
html,body{width:1200px;height:2400px;overflow:hidden;background:var(--white)}
body{position:relative;font-family:"Open Sans",Arial,sans-serif;color:var(--ink)}
.abs{position:absolute}
h1,h2,h3,h4{font-family:"Raleway",Arial,sans-serif;font-weight:500}

/* header */
.site-header{left:0;top:0;width:1200px;height:118px;background:var(--white)}
.brand{left:160px;top:36px;display:flex;align-items:center;gap:14px;font-family:"Raleway",sans-serif;font-weight:600;font-size:38px;color:var(--pink)}
.brand-dot{width:34px;height:34px;border-radius:50%;background:var(--orange)}
.search{left:824px;top:70px;width:229px;height:32px;border:1px solid #ccc;border-radius:2px;font-size:11px;color:#999;padding:8px 10px}
.search svg{position:absolute;right:9px;top:8px}

/* nav */
.main-nav{left:0;top:118px;width:1200px;height:50px;background:linear-gradient(#ee3568,var(--pink-dark))}
.main-nav a{position:absolute;top:0;height:50px;line-height:50px;color:var(--white);font-family:"Raleway",sans-serif;font-size:16px;font-weight:500;text-decoration:none;transform:translateX(-50%);white-space:nowrap}
.nav-home{left:149px!important;width:110px;transform:none!important;text-align:center;background:var(--yellow)}
.nav-sep{top:0;width:1px;height:50px;background:rgba(255,255,255,.25)}

/* hero */
.hero{left:0;top:168px;width:1200px;height:437px;background:linear-gradient(120deg,#5c6658 0%,#8e9490 35%,#b9bdbd 55%,#6f7170 80%,#3c3c3c 100%)}
.hero-title{left:0;top:300px;width:1200px;text-align:center;color:var(--white);font-family:"Raleway",sans-serif;font-weight:600;line-height:1}
.hero-title .l1{display:block;font-size:50px;letter-spacing:1px}
.hero-title .l2{display:block;font-size:40px;margin-top:6px;letter-spacing:1px}
.btn{display:inline-block;color:var(--white);font-family:"Raleway",sans-serif;font-weight:600;text-align:center}
.hero-btn{left:536px;top:413px;width:130px;height:35px;line-height:35px;font-size:14px;background:var(--teal-deep)}
.dots{left:560px;top:563px;display:flex;gap:6px}
.dots span{width:16px;height:16px;border-radius:50%;background:var(--white)}
.dots span.off{background:transparent;border:2px solid var(--white)}

/* welcome */
.welcome-deco{left:710px;top:605px;width:490px;height:328px;background:radial-gradient(ellipse at 60% 55%,#e4e4e4 0%,#f2f2f2 50%,#fff 75%)}
.welcome h2{left:149px;top:662px;font-size:30px;color:var(--ink)}
.welcome p{left:149px;width:555px;font-size:14px;line-height:22px;color:var(--muted)}
.donations h2{left:757px;top:662px;font-size:26px}
.bar{left:758px;top:714px;width:301px;height:22px;border:3px solid var(--yellow);border-radius:12px;background:var(--white);overflow:hidden}
.bar i{display:block;width:92%;height:100%;background:var(--pink)}
.ticks{left:762px;top:736px;width:270px;height:8px;background:repeating-linear-gradient(90deg,#999 0 1px,transparent 1px 6px);opacity:.5}
.amt{font-size:14px;font-weight:600;color:var(--ink)}
.donate-btn{left:762px;top:790px;width:137px;height:39px;line-height:39px;font-size:14px;background:linear-gradient(var(--orange),#e24d1b)}

/* video feeds */
.videos{left:0;top:933px;width:1200px;height:365px;background:linear-gradient(110deg,var(--orange) 0%,#ec4545 50%,var(--pink) 100%)}
.videos h2{left:150px;top:972px;font-size:26px;color:var(--white)}
.video-card{width:208px}
.video-thumb{width:208px;height:122px;border:3px solid var(--white);position:relative;background:linear-gradient(135deg,#7d8a86,#4a4f52)}
.video-thumb .play{position:absolute;left:84px;top:40px;width:38px;height:38px;border-radius:50%;background:var(--white)}
.video-thumb .play:after{content:"";position:absolute;left:15px;top:11px;border-left:12px solid #222;border-top:8px solid transparent;border-bottom:8px solid transparent}
.video-card h3{font-family:"Open Sans",sans-serif;font-weight:400;font-size:15px;color:var(--white);margin-top:9px}
.video-card p{font-size:11.5px;line-height:18px;color:rgba(255,255,255,.85);margin-top:4px}
.video-card .more{font-size:11px;color:var(--white);margin-top:14px;display:block}

/* features */
.features{left:0;top:1298px;width:1200px;height:299px;background:var(--yellow)}
.feature-photo{width:198px;height:198px;border-radius:50%;border:2px solid var(--white);padding:6px}
.feature-photo div{width:100%;height:100%;border-radius:50%}
.feature h3{font-size:22px;line-height:27px;color:var(--white)}
.feature p{font-size:12px;line-height:17px;color:rgba(255,255,255,.92);width:235px;margin-top:10px}

/* blogs */
.blogs h2{left:149px;top:1665px;font-size:26px}
.blog-img{width:179px;height:115px}
.blog-entry h3{font-family:"Open Sans",sans-serif;font-weight:400;font-size:17px;color:var(--ink)}
.blog-entry p{font-size:12.5px;line-height:20px;color:var(--muted);width:390px;margin-top:6px}
.blog-entry .more{font-size:13px;color:var(--pink);display:block;margin-top:4px}
.gps{left:736px;top:1670px;width:320px;height:333px;border:1px solid var(--line)}
.gps h3{height:46px;line-height:46px;padding-left:28px;background:linear-gradient(var(--teal-light),var(--teal-deep));color:var(--white);font-size:20px}
.gps-map{position:absolute;left:36px;top:70px;width:270px;height:240px;border-radius:40% 45% 30% 40%;background:linear-gradient(135deg,#9fdcaa 0%,#4fb7b8 45%,#2d7fc1 100%)}

/* footer */
.site-footer{left:0;top:2106px;width:1200px;height:233px;background:var(--teal)}
.foot-col h4{font-size:16px;color:var(--white);font-weight:500}
.foot-col ul{list-style:none;margin-top:12px}
.foot-col li{font-size:12px;line-height:23px;color:var(--white)}
.foot-col li svg{vertical-align:-2px;margin-right:5px}
.social{width:36px;height:36px;border-radius:50%;background:#226b6b}
.bottom-bar{left:0;top:2339px;width:1200px;height:61px;background:var(--teal-light);font-size:10.5px;color:rgba(255,255,255,.85)}
</style>
</head>
<body>

<header class="site-header abs">
  <div class="brand abs"><span class="brand-dot"></span>Open Road Ride</div>
  <div class="search abs">Search here
    <svg width="15" height="15" viewBox="0 0 15 15"><circle cx="6" cy="6" r="4.5" fill="none" stroke="#888" stroke-width="1.6"/><line x1="9.5" y1="9.5" x2="14" y2="14" stroke="#888" stroke-width="1.8"/></svg>
  </div>
</header>

<nav class="main-nav abs">
  <a class="nav-home" href="#">HOME</a>
  <span class="nav-sep abs" style="left:410px"></span>
  <span class="nav-sep abs" style="left:557px"></span>
  <span class="nav-sep abs" style="left:695px"></span>
  <span class="nav-sep abs" style="left:800px"></span>
  <span class="nav-sep abs" style="left:913px"></span>
  <a href="#" style="left:336px">ABOUT US</a>
  <a href="#" style="left:483px">DONATION</a>
  <a href="#" style="left:627px">GALLERY</a>
  <a href="#" style="left:749px">BLOG</a>
  <a href="#" style="left:859px">VIDEO</a>
  <a href="#" style="left:997px">RESOURCES</a>
</nav>

<section class="hero abs" role="img" aria-label="Two riders on motorcycles side by side on an open country road"></section>
<h1 class="hero-title abs"><span class="l1">TWO MATES. TWO BIKES.</span><span class="l2">ONE LONG ROAD</span></h1>
<a class="btn hero-btn abs">READ MORE</a>
<div class="dots abs"><span class="off"></span><span></span><span></span><span></span></div>

<section class="welcome">
  <div class="welcome-deco abs" role="img" aria-label="Faint motorcycle silhouette in the background"></div>
  <h2 class="abs">WELCOME TO OPEN ROAD RIDE</h2>
  <p class="abs" style="top:712px">Fusce ultricies orci ac feugiat suscipit leo massa sodales velit et scelerisque mi tortor at ipsum cligula augue bibendum accumsan vestibulum</p>
  <p class="abs" style="top:772px">ut commodo a mi Morbi ornare gravida elit Integer congue augue et malesuada iaculis ipsum dui aliquet felis at cursus magna nisl nec elit Praesent elementum elit at tellus nec ultricies sit amet porttitor mattis enim In massa libero</p>
</section>

<section class="donations">
  <h2 class="abs">DONATIONS</h2>
  <div class="bar abs"><i></i></div>
  <div class="ticks abs"></div>
  <span class="amt abs" style="left:762px;top:750px">$0</span>
  <span class="amt abs" style="left:994px;top:746px">$25.95</span>
  <a class="btn donate-btn abs">DONATE NOW</a>
</section>

<section class="videos abs"></section>
<h2 class="abs" style="left:150px;top:972px;font-size:26px;color:#fff">VIDEO FEEDS</h2>
<article class="video-card abs" style="left:147px;top:1016px">
  <div class="video-thumb" role="img" aria-label="Riding couple on a red motorcycle"><span class="play"></span></div>
  <h3>Praesent elementum elit</h3>
  <p>scelerisque mi tortor at ipsum cligula augue bibendum vestibulu</p>
  <span class="more">READ MORE</span>
</article>
<article class="video-card abs" style="left:381px;top:1016px">
  <div class="video-thumb" role="img" aria-label="Racer leaning into a corner on a track"><span class="play"></span></div>
  <h3>Cum sociis natoqu</h3>
  <p>scelerisque mi tortor at ipsum cligula augue bibendum vestibulu</p>
  <span class="more">READ MORE</span>
</article>
<article class="video-card abs" style="left:614px;top:1016px">
  <div class="video-thumb" role="img" aria-label="Two riders in a workshop"><span class="play"></span></div>
  <h3>Sed porta Suspendi</h3>
  <p>scelerisque mi tortor at ipsum cligula augue bibendum vestibulu</p>
  <span class="more">READ MORE</span>
</article>
<article class="video-card abs" style="left:846px;top:1016px">
  <div class="video-thumb" role="img" aria-label="Two riders heading down a road from behind"><span class="play"></span></div>
  <h3>Quisque dignissim</h3>
  <p>scelerisque mi tortor at ipsum cligula augue bibendum vestibulu</p>
  <span class="more">READ MORE</span>
</article>

<section class="features abs"></section>
<article class="feature">
  <div class="feature-photo abs" style="left:135px;top:1336px"><div role="img" aria-label="Touring motorcycle on a mountain road" style="background:linear-gradient(#8fa9c4,#c7d3d8 50%,#6b6f6a)"></div></div>
  <h3 class="abs" style="left:353px;top:1355px">Oh yeah, it's that good<br>See for yourself.</h3>
  <p class="abs" style="left:354px;top:1425px">Donec ullamcorper nulla non metus auctor fringilla. Vestibulum id ligula porta felis euismod semper. Praesent commodo cursus magna, vel scelerisque nisl consectetur. Fusce</p>
</article>
<article class="feature">
  <div class="feature-photo abs" style="left:597px;top:1336px"><div role="img" aria-label="Dirt bike rider on a gravel track" style="background:linear-gradient(#6b7a5c,#b7b1a3 55%,#d8d2c6)"></div></div>
  <h3 class="abs" style="left:814px;top:1355px">And lastly, this one.<br>Checkmate.</h3>
  <p class="abs" style="left:815px;top:1425px">Donec ullamcorper nulla non metus auctor fringilla. Vestibulum id ligula porta felis euismod semper. Praesent commodo cursus magna, vel scelerisque nisl consectetur. Fusce</p>
</article>

<section class="blogs">
  <h2 class="abs">LATEST BLOGS</h2>
  <article class="blog-entry">
    <div class="blog-img abs" style="left:149px;top:1725px;background:linear-gradient(#f3a12e,#d25a12 55%,#2b1a10)" role="img" aria-label="Riders with bikes at sunset"></div>
    <div class="abs" style="left:344px;top:1722px">
      <h3>Mauris vel lacus vitae felis vestibulum</h3>
      <p>volutpat Etiam est nunc venenatis in tristique eu imperdiet ac nisl Cum sociis natoque penatibus et magnis dis parturient nascetur ridiculus</p>
      <span class="more">READ MORE</span>
    </div>
  </article>
  <article class="blog-entry">
    <div class="blog-img abs" style="left:149px;top:1877px;background:linear-gradient(135deg,#d9a06a,#a56a3c 60%,#6e4426)" role="img" aria-label="Two motorcycles parked on a sandy road"></div>
    <div class="abs" style="left:344px;top:1874px">
      <h3>Donec dictum lectus non odio</h3>
      <p>volutpat Etiam est nunc venenatis in tristique eu imperdiet ac nisl Cum sociis natoque penatibus et magnis dis parturient nascetur ridiculus</p>
      <span class="more">READ MORE</span>
    </div>
  </article>
  <aside class="gps abs">
    <h3>GPS TRACKER</h3>
    <div class="gps-map" role="img" aria-label="Map of Australia with route location pins"></div>
  </aside>
</section>

<footer class="site-footer abs">
  <div class="foot-col abs" style="left:160px;top:48px"><h4>ABOUT</h4><ul><li>Aorttitor mattis</li><li>Enim In massa</li><li>Aibero</li><li>Interdum ne</li></ul></div>
  <div class="foot-col abs" style="left:331px;top:48px"><h4>SUBLINKS</h4><ul><li>Donations</li><li>Our Map</li><li>Blogs</li><li>Video Feed</li></ul></div>
  <div class="foot-col abs" style="left:506px;top:48px"><h4>RESOURCES</h4><ul><li>FAQ</li><li>Support</li><li>Testimonials</li><li>Contact</li></ul></div>
  <div class="foot-col abs" style="left:683px;top:48px"><h4>CONTACT US</h4><ul>
    <li>48 Wattle Grove Lane</li>
    <li>PO Box 2210 Larkfield, NSW 2790</li>
    <li><svg width="12" height="12" viewBox="0 0 12 12"><path d="M3 1l2 2.5-1.2 1.4a7 7 0 003.3 3.3L8.5 7 11 9l-1.2 2C5.5 11 1 6.5 1 2.2z" fill="#fff"/></svg>(02) 5550 1874</li>
    <li><svg width="12" height="10" viewBox="0 0 12 10"><rect x="0.5" y="0.5" width="11" height="9" fill="none" stroke="#fff"/><path d="M0.5 0.5L6 5l5.5-4.5" fill="none" stroke="#fff"/></svg>team@openroadride.org</li>
  </ul></div>
  <div class="foot-col abs" style="left:888px;top:48px"><h4>FOLLOW US</h4></div>
  <span class="social abs" style="left:888px;top:74px"></span>
  <span class="social abs" style="left:931px;top:74px"></span>
  <span class="social abs" style="left:976px;top:74px"></span>
  <span class="social abs" style="left:1019px;top:74px"></span>
</footer>
<div class="bottom-bar abs"><span class="abs" style="left:152px;top:21px">© 2016 Company Name  All right reserved</span></div>

</body>
</html>
```